Marcus & Fiona's Midsummer Unwind Evening

Invitation to a party 60-80 people at a private residence. Age range 30-40s.

Themes: summer/casual/Australian backyard/local community

**For delivery via both email and printed copy**
Would like one document suitable for both purposes or two versions for electronic or paper invitation. I will arrange printing so please prepare it in a suitable format.

Specimen text attached. Address and phone contact to follow by message with successful bidder

Thanks!
Marcus

Target Market(s)

Locals, friends. Party attendees will typicaly be parents in their forties who who be leaving the kids at home for a relaxed party night, and walking home afterward

Industry/Entity Type

Community

Font styles to use
Sans Serif

Requirements
Should not have
• Cliche Australiana imagery. No kangaroos etc

```html
<!DOCTYPE html>
<html lang="en">
<head>
<meta charset="utf-8">
<title>Marcus &amp; Fiona's Midsummer Unwind Evening – Invitation</title>
<link rel="stylesheet" href="https://fonts.googleapis.com/css2?family=Lato:wght@300;400;700;900&family=Great+Vibes&display=swap">
<style>
  :root {
    --backdrop: #e4d6e8;
    --card-navy: #110f33;
    --accent-pink: #e0137e;
    --text-light: #ffffff;
    --text-soft: #b9b7cc;
    --rule: #8c8aa6;
  }
  * { margin: 0; padding: 0; box-sizing: border-box; }
  html, body { width: 1200px; height: 515px; overflow: hidden; background: var(--backdrop); }
  .canvas { position: relative; width: 1200px; height: 515px; font-family: "Lato", sans-serif; }

  .card {
    position: absolute; top: 38px; width: 340px; height: 440px;
    background: var(--card-navy); color: var(--text-light); text-align: center;
  }
  .card--front { left: 130px; }
  .card--back { left: 730px; }

  .ornament { position: absolute; left: 50%; transform: translateX(-50%); background: var(--accent-pink); opacity: .55; border-radius: 40%; }
  .ornament--top { top: 8px; width: 136px; height: 52px; }
  .ornament--divider { top: 262px; width: 210px; height: 14px; border-radius: 7px; }
  .ornament--bottom { top: 380px; width: 136px; height: 52px; }

  .headline { position: absolute; top: 93px; width: 100%; font-weight: 900; font-size: 14px; color: var(--accent-pink); letter-spacing: .2px; }
  .subline { position: absolute; top: 110px; width: 100%; font-size: 10px; color: var(--accent-pink); }
  .hosts { position: absolute; top: 152px; width: 100%; font-weight: 300; font-size: 17px; color: var(--text-soft); }
  .event-title { position: absolute; top: 174px; width: 100%; font-family: "Great Vibes", cursive; font-size: 21px; color: var(--accent-pink); }
  .audience { position: absolute; top: 199px; width: 100%; font-size: 7.5px; color: var(--text-soft); }
  .clock-icon { position: absolute; top: 288px; left: 158px; }
  .when { position: absolute; top: 320px; width: 100%; font-size: 10px; color: var(--text-light); }
  .when .sep { margin: 0 8px; }
  .where { position: absolute; top: 340px; width: 100%; font-weight: 700; font-size: 11px; }

  .details { position: absolute; top: 78px; left: 67px; width: 206px; height: 123px; border: 1px solid var(--rule); padding-top: 6px; }
  .details__row { height: 14.5px; line-height: 14.5px; font-size: 7px; margin: 0 22px; border-bottom: 1px solid var(--rule); }
  .details__row:last-child { border-bottom: none; }
  .details__row--head { font-weight: 700; color: var(--text-light); }
  .details__row--note { color: var(--text-soft); font-weight: 300; }

  .contact { position: absolute; top: 232px; left: 67px; width: 206px; height: 62px; border: 1px solid var(--rule); }
  .phone-icon { position: absolute; top: 218px; left: 155px; background: var(--card-navy); padding: 0 6px; }
  .contact__ask { position: absolute; top: 20px; width: 100%; font-size: 6.5px; color: var(--text-soft); }
  .contact__rule { position: absolute; top: 31px; left: 40px; right: 40px; border-top: 1px solid var(--rule); }
  .contact__numbers { position: absolute; top: 40px; width: 100%; font-size: 6.5px; color: var(--text-soft); }
  .friends-note { position: absolute; top: 334px; left: 90px; width: 160px; font-size: 6.5px; line-height: 1.3; color: var(--text-soft); }
</style>
</head>
<body>
<main class="canvas">
  <section class="card card--front">
    <div class="ornament ornament--top" role="img" aria-label="Pink decorative flourish"></div>
    <h1 class="headline">LEAVE THE KIDS AT HOME</h1>
    <p class="subline">and Let Your Hair Down At:</p>
    <p class="hosts">Marcus &amp; Fiona's</p>
    <h2 class="event-title">Midsummer Unwind Evening</h2>
    <p class="audience">For Brookvale Heights and friends</p>
    <div class="ornament ornament--divider" role="img" aria-label="Pink decorative divider flourish"></div>
    <svg class="clock-icon" width="24" height="24" viewBox="0 0 24 24" aria-hidden="true">
      <circle cx="11" cy="11" r="9" fill="none" stroke="#fff" stroke-width="1.6"/>
      <path d="M11 6v5h4" fill="none" stroke="#fff" stroke-width="1.6"/>
      <rect x="14" y="14" width="9" height="9" rx="1" fill="#fff"/>
      <rect x="15.5" y="17" width="6" height="4.5" fill="#110f33"/>
    </svg>
    <p class="when">Saturday 2 January<span class="sep">|</span>From 6pm 'till late</p>
    <p class="where">14 Wattle Lane, Brookvale Heights</p>
    <div class="ornament ornament--bottom" role="img" aria-label="Pink decorative flourish"></div>
  </section>

  <section class="card card--back">
    <div class="details">
      <p class="details__row details__row--head">Child-free event</p>
      <p class="details__row details__row--head">DRESS</p>
      <p class="details__row details__row--note">summer casual, bare feet welcome</p>
      <p class="details__row details__row--head">Cocktail food provided</p>
      <p class="details__row details__row--note">BYO but only if you insist</p>
      <p class="details__row details__row--head">RSVP</p>
      <p class="details__row details__row--note">for catering would be nice.</p>
    </div>
    <div class="contact">
      <p class="contact__ask">TEXT US before Xmas please.</p>
      <div class="contact__rule"></div>
      <p class="contact__numbers">Marcus | +61 400 555 012 &nbsp;or&nbsp; Fiona | +61 400 555 034</p>
    </div>
    <svg class="phone-icon" width="30" height="26" viewBox="0 0 30 26" aria-hidden="true">
      <rect x="9" y="1" width="12" height="22" rx="2" fill="none" stroke="#fff" stroke-width="1.6"/>
      <rect x="11" y="4" width="8" height="14" fill="#fff"/>
      <circle cx="15" cy="20.5" r="1" fill="#fff"/>
    </svg>
    <p class="friends-note">If you have some friends or neighbours that you like to hang out with, we would love to meet. Bring them with you!</p>
  </section>
</main>
</body>
</html>
```